indépendant en tant que Massothérapeute et Préparateur Mental, j'ai besoin de ...

Massothérapeute et préparateur mental indépendant, je recherche une carte de visite sobre et dynamique, sans images liées au massage ou à la préparation mentale mais intégrant mon logo. Les couleurs que j'aime bien sont : Blanc, gris, anthracite, noir et jaune

Contact Information for Business Card

carte de préférence Horizontale
neutre qui puisse toucher le deux domaines Massothérapie et préparation mentale

Requirements
Must have
• mon projet doit intégrer au recto:
LOGO
Loïc Bardèze
078 513 26 48
info@loicbardeze.ch
et éventuellement www.loicbardeze.ch

et au verso les deux adresses:

Chemin des Ormilles 7B
1400 Yverdon-les-Bains

Route de la Gravière 9
1700 Fribourg

Should not have
• mon projet ne doit pas contenir d'image en liens avec le massage ni la préparation mentale.

```html
<!DOCTYPE html>
<html lang="fr">
<head>
<meta charset="utf-8">
<title>Loïc Bardèze – Cartes de visite</title>
<link href="https://fonts.googleapis.com/css2?family=Michroma&family=Montserrat:wght@500;600&family=Arimo&display=swap" rel="stylesheet">
<style>
  :root {
    --stage: #b4b4b4;
    --anthracite: #222123;
    --anthracite-soft: #2c2b2d;
    --paper: #ffffff;
    --ink: #111111;
    --rule: #9a9a9a;
    --light-text: #e6e6e6;
  }
  * { margin: 0; padding: 0; box-sizing: border-box; }
  html, body { width: 1200px; height: 1200px; overflow: hidden; }
  body { background: var(--stage); position: relative; font-family: "Arimo", Arial, sans-serif; }

  .card { position: absolute; top: 303px; width: 368px; height: 594px; }
  .card--back { left: 200px; background: var(--anthracite); }
  .card--front { left: 599px; width: 364px; background: var(--paper); color: var(--ink); }

  .back-texture {
    position: absolute; left: 0; top: 90px; width: 100%; height: 500px;
    background: linear-gradient(180deg, var(--anthracite) 0%, var(--anthracite-soft) 50%, var(--anthracite) 100%);
  }
  .back-brand { position: absolute; left: 0; right: 0; top: 500px; text-align: center; }
  .back-brand .brand-name {
    font-family: "Montserrat", sans-serif; font-weight: 600;
    font-size: 24px; letter-spacing: 1px; color: var(--light-text);
  }
  .back-brand .brand-tagline {
    margin-top: 6px; font-family: "Montserrat", sans-serif; font-weight: 500;
    font-size: 11px; letter-spacing: 1.2px; text-transform: uppercase; color: var(--light-text);
  }

  .front-brand { position: absolute; left: 40px; top: 133px; display: flex; align-items: center; gap: 12px; }
  .front-brand .brand-mark { width: 26px; height: 26px; background: var(--ink); }
  .front-brand .brand-name {
    font-family: "Montserrat", sans-serif; font-weight: 600; font-size: 19px; letter-spacing: 0.5px;
  }
  .front-brand .brand-tagline {
    font-family: "Montserrat", sans-serif; font-weight: 500; font-size: 7px;
    letter-spacing: 0.6px; text-transform: uppercase; margin-top: 2px;
  }

  .holder-name {
    position: absolute; left: 0; right: 0; top: 298px; text-align: center;
    font-family: "Michroma", sans-serif; font-size: 25px; letter-spacing: 1px;
  }
  .contact-icons { position: absolute; left: 0; right: 0; top: 349px; display: flex; justify-content: center; align-items: center; gap: 4px; }
  .contact-icons .rule { width: 52px; height: 1px; background: var(--rule); margin: 0 4px; }
  .contact-icons svg { width: 25px; height: 25px; display: block; }

  .contact-list { position: absolute; left: 0; right: 0; top: 386px; text-align: center; font-size: 17px; line-height: 21.5px; }
  .divider { position: absolute; left: 88px; width: 194px; top: 460px; height: 1px; background: var(--rule); }
  .addresses { position: absolute; left: 0; right: 0; top: 470px; text-align: center; font-size: 17px; line-height: 21px; }
  .addresses p + p { margin-top: 10px; }
</style>
</head>
<body>
  <section class="card card--back" aria-label="Verso">
    <div class="back-texture" role="img" aria-label="Motif discret du monogramme en gris anthracite"></div>
    <div class="back-brand">
      <div class="brand-name">Loïc Bardèze</div>
      <div class="brand-tagline">Massothérapeute / Préparateur Mental</div>
    </div>
  </section>

  <section class="card card--front" aria-label="Recto">
    <div class="front-brand">
      <span class="brand-mark"></span>
      <div>
        <div class="brand-name">Loïc Bardèze</div>
        <div class="brand-tagline">Massothérapeute / Préparateur Mental</div>
      </div>
    </div>

    <h1 class="holder-name">LOÏC BARDÈZE</h1>

    <div class="contact-icons">
      <span class="rule"></span>
      <svg viewBox="0 0 25 25" aria-label="Téléphone">
        <rect width="25" height="25" rx="3" fill="#111"/>
        <path d="M5 10c0-3 3-4 7.5-4S20 7 20 10h-3.5l-.5-1.5h-7L8.5 10z" fill="#fff"/>
        <rect x="7" y="11" width="11" height="8" rx="1" fill="#fff"/>
        <circle cx="12.5" cy="15" r="2" fill="#111"/>
      </svg>
      <svg viewBox="0 0 25 25" aria-label="Courriel">
        <rect width="25" height="25" rx="3" fill="#111"/>
        <rect x="5" y="7.5" width="15" height="10" fill="none" stroke="#fff" stroke-width="1.3"/>
        <path d="M5 7.5l7.5 6 7.5-6M5 17.5l5.5-5M20 17.5l-5.5-5" fill="none" stroke="#fff" stroke-width="1.1"/>
      </svg>
      <svg viewBox="0 0 25 25" aria-label="Site web">
        <rect width="25" height="25" rx="3" fill="#111"/>
        <circle cx="12.5" cy="12.5" r="7" fill="#fff"/>
        <ellipse cx="12.5" cy="12.5" rx="3" ry="7" fill="none" stroke="#111" stroke-width="1"/>
        <path d="M5.5 12.5h14" stroke="#111" stroke-width="1"/>
      </svg>
      <span class="rule"></span>
    </div>

    <div class="contact-list">
      <p>078 513 26 48</p>
      <p>info@loicbardeze.ch</p>
      <p>www.loicbardeze.ch</p>
    </div>

    <div class="divider"></div>

    <div class="addresses">
      <p>Chemin des Ormilles 7B<br>1400 Yverdon-les-Bains</p>
      <p>Route de la Gravière 9<br>1700 Freiburg</p>
    </div>
  </section>
</body>
</html>
```